Business Card Design For A Renovation Contractor Company

We need a business card for a new company based in Singapore, our company name is "RB Tolvane". We are a renovation contractor that builds designs into reality. We build more of F&B restaurants, retail stores and commercial offices. We work very closely with designers. The final design should communicate to our client that we are a company that you can trust, that will plan and complete your project without giving you a headache. I like my client to remember my company as "RB". The beauty of SIMPLE is important.

Industry/Entity Type

Contractor

Requirements
Nice to have
• Black or Red base

```html
<!DOCTYPE html>
<html lang="en">
<head>
<meta charset="utf-8">
<title>RB Tolvane Business Card</title>
<link rel="stylesheet" href="https://fonts.googleapis.com/css2?family=Didact+Gothic&family=Montserrat:wght@700&display=swap">
<style>
  :root {
    --brand-red: #ec1c24;
    --ink: #1a1a1a;
    --grey-text: #4a4a4a;
    --rule: #c9c9c9;
    --card-white: #ffffff;
    --backdrop: #e9e9ee;
  }
  * { box-sizing: border-box; margin: 0; padding: 0; }
  html, body {
    width: 1200px; height: 987px; overflow: hidden;
    background: var(--backdrop);
  }
  .stage {
    width: 1200px; height: 987px;
    display: flex; flex-direction: column; align-items: center; justify-content: center;
    gap: 44px;
  }
  .card {
    width: 760px; height: 434px;
    border-radius: 34px;
    position: relative;
    overflow: hidden;
    box-shadow: 0 6px 18px rgba(0,0,0,0.12);
  }

  /* Front */
  .card-front {
    background: var(--card-white);
    font-family: "Didact Gothic", sans-serif;
    color: var(--grey-text);
  }
  .rule {
    position: absolute; left: 70px; right: 70px; height: 1px;
    background: var(--rule);
  }
  .rule-top { top: 156px; }
  .rule-bottom { bottom: 40px; }
  .brand {
    position: absolute; top: 34px; left: 0; right: 0;
    display: flex; align-items: center; justify-content: center; gap: 18px;
  }
  .brand-dot {
    width: 44px; height: 44px; border-radius: 50%;
    background: var(--brand-red);
  }
  .brand-name {
    font-size: 64px; line-height: 1; color: var(--ink);
  }
  .tagline {
    position: absolute; top: 118px; left: 0; right: 0;
    text-align: center; font-size: 22px; line-height: 1.2; color: var(--ink);
    letter-spacing: 0.5px;
  }
  .person {
    position: absolute; top: 178px; left: 0; right: 0; text-align: center;
    font-size: 26px;
  }
  .person-name { font-family: "Montserrat", sans-serif; font-weight: 700; color: var(--ink); }
  .person-title { color: var(--brand-red); }
  .contacts {
    position: absolute; top: 236px; left: 0; right: 0;
    display: flex; flex-direction: column; align-items: center; gap: 12px;
    font-size: 22px;
  }
  .contact-row { display: flex; gap: 26px; align-items: center; }
  .contact-item { display: flex; align-items: center; gap: 8px; }
  .contact-item svg { width: 18px; height: 18px; fill: var(--brand-red); }

  /* Back */
  .card-back { background: var(--brand-red); }
  .back-brand {
    position: absolute; top: 150px; left: 0; right: 0;
    display: flex; align-items: center; justify-content: center; gap: 20px;
  }
  .back-dot { width: 56px; height: 56px; border-radius: 50%; background: var(--ink); }
  .back-name {
    font-family: "Didact Gothic", sans-serif; font-size: 76px; line-height: 1;
    color: var(--ink);
  }
  .back-web {
    position: absolute; bottom: 80px; left: 0; right: 0; text-align: center;
    font-family: "Didact Gothic", sans-serif; font-size: 22px; letter-spacing: 6px;
    color: var(--card-white);
  }
</style>
</head>
<body>
<main class="stage">
  <section class="card card-front" aria-label="Business card front">
    <div class="brand">
      <span class="brand-dot"></span>
      <span class="brand-name">RB Tolvane</span>
    </div>
    <p class="tagline">turning plans into built spaces</p>
    <div class="rule rule-top"></div>
    <p class="person"><span class="person-name">Your Name,</span> <span class="person-title">Title</span></p>
    <div class="contacts">
      <div class="contact-row">
        <span class="contact-item">
          <svg viewBox="0 0 24 24" aria-hidden="true"><path d="M6.6 10.8a15 15 0 0 0 6.6 6.6l2.2-2.2a1 1 0 0 1 1-.25 11.4 11.4 0 0 0 3.6.57 1 1 0 0 1 1 1V20a1 1 0 0 1-1 1A17 17 0 0 1 3 4a1 1 0 0 1 1-1h3.5a1 1 0 0 1 1 1c0 1.25.2 2.45.57 3.57a1 1 0 0 1-.25 1z"/></svg>
          123-456-0789
        </span>
        <span class="contact-item">
          <svg viewBox="0 0 24 24" aria-hidden="true"><path d="M7 2h10a2 2 0 0 1 2 2v16a2 2 0 0 1-2 2H7a2 2 0 0 1-2-2V4a2 2 0 0 1 2-2zm0 3v12h10V5zm5 13.5a1.2 1.2 0 1 0 0 2.4 1.2 1.2 0 0 0 0-2.4z"/></svg>
          123-456-0789
        </span>
      </div>
      <div class="contact-row">
        <span class="contact-item">
          <svg viewBox="0 0 24 24" aria-hidden="true"><path d="M3 5h18a1 1 0 0 1 1 1v12a1 1 0 0 1-1 1H3a1 1 0 0 1-1-1V6a1 1 0 0 1 1-1zm9 7.5L20 7H4z"/></svg>
          info@rbtolvane.com
        </span>
        <span class="contact-item">
          <svg viewBox="0 0 24 24" aria-hidden="true"><path d="M12 2a10 10 0 1 0 0 20 10 10 0 0 0 0-20zm6.9 9h-3a15 15 0 0 0-1.4-6 8 8 0 0 1 4.4 6zM12 4.1A13 13 0 0 1 13.9 11h-3.8A13 13 0 0 1 12 4.1zM9.5 5a15 15 0 0 0-1.4 6h-3a8 8 0 0 1 4.4-6zM5.1 13h3a15 15 0 0 0 1.4 6 8 8 0 0 1-4.4-6zm6.9 6.9A13 13 0 0 1 10.1 13h3.8A13 13 0 0 1 12 19.9zm2.5-.9a15 15 0 0 0 1.4-6h3a8 8 0 0 1-4.4 6z"/></svg>
          www.rbtolvane.com
        </span>
      </div>
      <div class="contact-row">
        <span class="contact-item">Street Name, City Name, State Zip Code</span>
      </div>
    </div>
    <div class="rule rule-bottom"></div>
  </section>

  <section class="card card-back" aria-label="Business card back">
    <div class="back-brand">
      <span class="back-dot"></span>
      <span class="back-name">RB Tolvane</span>
    </div>
    <p class="back-web">www.rbtolvane.com</p>
  </section>
</main>
</body>
</html>
```